Business Recognition Design

We need a design for a recognition to be given to business leaders in our community.
The recognition shall be made on a brass plaque on wood panel background (picture attached, please use it as a background), and all drawing must be in vectors and only one color (black).
It should also have a logo on the top and signature on the right bottom.
The text is enclosed in DOC file.
Updates

Reason: just to be able to find the best solution

Reason: None of the suggestion is good enough. Logo in general is too big in comparison with the rest of the plate.

Industry/Entity Type

Business

Requirements
Must have
• - standard Windows font (or possibility to install the same font on Windows), as the name on the recognition shall be printed in the same font
Nice to have
• - some graphic element (in curves) representing achievements in business
- should look great :)

```html
<!DOCTYPE html>
<html lang="en">
<head>
<meta charset="utf-8">
<title>Recognition Plaque – The Best Entrepreneur in 2013</title>
<link href="https://fonts.googleapis.com/css2?family=Ubuntu:wght@400;500;700&display=swap" rel="stylesheet">
<style>
  :root {
    --wood-dark: #5a3216;
    --wood-mid: #7c4a22;
    --wood-light: #9a6334;
    --brass-deep: #b88d2c;
    --brass-mid: #d8b24e;
    --brass-light: #f2d98a;
    --brass-edge: #8a6418;
    --screw-rim: #6e4e12;
    --ink: #141208;
  }
  * { margin: 0; padding: 0; box-sizing: border-box; }
  html, body {
    width: 1200px;
    height: 932px;
    overflow: hidden;
    background: #ffffff;
  }
  .plaque {
    position: relative;
    width: 1200px;
    height: 932px;
    background: linear-gradient(180deg, var(--wood-light) 0%, var(--wood-mid) 40%, var(--wood-dark) 100%);
    font-family: "Ubuntu", "Segoe UI", sans-serif;
    color: var(--ink);
  }
  .brass-plate {
    position: absolute;
    left: 41px;
    top: 37px;
    width: 1118px;
    height: 855px;
    background:
      repeating-linear-gradient(90deg, rgba(255,255,255,0.05) 0 2px, rgba(0,0,0,0.03) 2px 5px),
      linear-gradient(135deg, var(--brass-deep) 0%, var(--brass-light) 30%, var(--brass-mid) 55%, var(--brass-light) 78%, var(--brass-deep) 100%);
    border: 2px solid var(--brass-edge);
    box-shadow: 0 4px 8px rgba(0,0,0,0.45), inset 0 0 0 3px rgba(255,240,190,0.35);
  }
  .screw {
    position: absolute;
    width: 22px;
    height: 22px;
    border-radius: 50%;
    background: radial-gradient(circle at 40% 38%, var(--brass-light) 0%, var(--brass-mid) 45%, var(--brass-deep) 100%);
    border: 3px solid var(--screw-rim);
  }
  .screw.top-left { left: 73px; top: 73px; }
  .screw.top-right { left: 1114px; top: 73px; }
  .screw.bottom-left { left: 73px; top: 829px; }
  .screw.bottom-right { left: 1114px; top: 829px; }

  .growth-icon {
    position: absolute;
    left: 522px;
    top: 100px;
    width: 156px;
    height: 146px;
  }
  .centered {
    position: absolute;
    left: 0;
    width: 1200px;
    text-align: center;
    white-space: nowrap;
  }
  .title {
    top: 268px;
    font-size: 80px;
    font-weight: 700;
    letter-spacing: 2px;
    line-height: 1;
  }
  .award {
    font-size: 48px;
    font-weight: 700;
    line-height: 1;
  }
  .award.line-one { top: 377px; }
  .award.line-two { top: 452px; }
  .dedication {
    top: 530px;
    font-size: 26px;
    line-height: 1;
  }
  .recipient {
    top: 580px;
    font-size: 46px;
    line-height: 1;
  }
  .recipient strong { font-weight: 700; }
  .citation {
    top: 648px;
    font-size: 28px;
    line-height: 37.5px;
  }
  .citation strong { font-weight: 700; }
  .date, .signatory {
    position: absolute;
    top: 808px;
    font-size: 25px;
    line-height: 1;
  }
  .date { left: 244px; }
  .date sup { font-size: 14px; vertical-align: 10px; }
  .signatory { right: 257px; }
</style>
</head>
<body>
  <main class="plaque">
    <div class="brass-plate"></div>
    <span class="screw top-left"></span>
    <span class="screw top-right"></span>
    <span class="screw bottom-left"></span>
    <span class="screw bottom-right"></span>

    <svg class="growth-icon" viewBox="0 0 156 146" aria-hidden="true">
      <g fill="var(--ink)">
        <rect x="0" y="20" width="9" height="126"/>
        <rect x="0" y="137" width="156" height="9"/>
        <rect x="22" y="98" width="14" height="32"/>
        <rect x="44" y="82" width="14" height="48"/>
        <rect x="66" y="90" width="14" height="40"/>
        <rect x="88" y="66" width="14" height="64"/>
        <rect x="110" y="48" width="14" height="82"/>
        <rect x="132" y="28" width="14" height="102"/>
        <polygon points="128,0 156,2 148,28"/>
      </g>
      <polyline points="16,82 50,58 72,70 104,40 120,46 146,12"
        fill="none" stroke="var(--ink)" stroke-width="8" stroke-linejoin="miter"/>
    </svg>

    <h1 class="centered title">RECOGNITION</h1>
    <p class="centered award line-one">The Best Entrepreneur</p>
    <p class="centered award line-two">in 2013</p>
    <p class="centered dedication">to</p>
    <p class="centered recipient">Mr. <strong>Daniel R. Whitford,</strong> MBA</p>
    <p class="centered citation">
      Under the leadership of Mr. Daniel R. Whitford, MBA<br>
      the company <strong>DR-WHITFORD Ltd</strong> has been selected<br>
      by a City Council as the best company of The City.
    </p>
    <p class="date">4<sup>th</sup> July, 2013</p>
    <p class="signatory">City Mayor</p>
  </main>
</body>
</html>
```